Business Cards Design for the electrical wholesaler: clean bold dynamic :)

We need a business card design that would follow our latest brand guidelines. As an electrical wholesaler we want to bring a fresh look and feel into the industry. The design should be clean bold and dynamic. It should come alive with the renewed energy of our green colour. Our grey colour should keep things balanced and complement the notion of maturity and responsibility. We employ Lato as a corporate font however are not bound by this font and we’re open to interpretation here.

Target Market(s)

Electrical contractors

Industry/Entity Type

Business

Contact Information for Business Card

Logo
Name & Surname: Halyna Dorosh
Job Title: Director of Marketing
Email: halya.dorosh@quillmail.example
Cell phone: XXX.XXX.XXXX
Address: 20517 - 87 Ave. Edmonton, AB, Canada. T6K 4N8
Business Phone: 780.555.0184
Website: www.brovix.example

Font styles to use
Other font styles liked:
• Lato

Requirements
Must have
• Logo & website
Nice to have
• Brand elements - some of them you may find in the attached Brand Guidelines (e.g. three lines on the background signifying "W")

```html
<!DOCTYPE html>
<html lang="en">
<head>
<meta charset="utf-8">
<title>Brovix Business Cards</title>
<link href="https://fonts.googleapis.com/css2?family=Lato:wght@400;700&display=swap" rel="stylesheet">
<style>
  :root {
    --brand-green: #8dc63f;
    --brand-grey: #4d4d4f;
    --text-grey: #5a5a5c;
    --muted-grey: #6b6b6d;
    --rule-grey: #555557;
    --paper: #ffffff;
    --bg-light: #e4e2dd;
    --bg-slate: #5d6d84;
  }
  * { margin: 0; padding: 0; box-sizing: border-box; }
  html, body { width: 1200px; height: 1000px; overflow: hidden; }
  body {
    position: relative;
    font-family: "Lato", Arial, sans-serif;
    background: linear-gradient(90deg, var(--bg-light) 0 598px, var(--bg-slate) 598px 100%);
  }
  .card {
    position: absolute;
    width: 510px;
    height: 290px;
    overflow: hidden;
  }
  .card--rounded { border-radius: 30px; }
  .card--front { background: var(--brand-green); }
  .card--back { background: var(--paper); }

  .rounded-front { left: 64px; top: 60px; }
  .rounded-back  { left: 64px; top: 427px; }
  .square-front  { left: 625px; top: 284px; width: 512px; height: 291px; }
  .square-back   { left: 625px; top: 640px; width: 512px; height: 292px; }

  .wordmark {
    position: absolute;
    display: flex;
    align-items: center;
    gap: 14px;
    font-weight: 400;
    letter-spacing: -0.5px;
    line-height: 1;
  }
  .wordmark__dot { border-radius: 50%; flex: none; }

  .card--front .wordmark {
    left: 0; right: 0; top: 0; bottom: 0;
    justify-content: center;
    font-size: 62px;
    color: var(--paper);
  }
  .card--front .wordmark__dot { width: 46px; height: 46px; background: var(--paper); }

  .card--back .wordmark {
    right: 32px; top: 26px;
    font-size: 46px;
    color: var(--brand-grey);
    gap: 10px;
  }
  .card--back .wordmark__dot { width: 34px; height: 34px; background: var(--brand-green); }

  .person { position: absolute; left: 26px; top: 92px; }
  .person__name { font-size: 26px; color: var(--text-grey); font-weight: 400; line-height: 1.1; }
  .person__title { font-size: 15px; color: var(--muted-grey); margin-top: 6px; }

  .divider {
    position: absolute;
    left: 223px; width: 254px; top: 143px;
    height: 2px; background: var(--rule-grey);
  }

  .address {
    position: absolute;
    right: 32px; top: 154px;
    font-size: 15px; color: var(--text-grey);
    text-align: right; line-height: 19px;
  }
  .address__pin { position: absolute; left: -24px; top: 2px; width: 11px; height: 15px; fill: var(--text-grey); }

  .contacts { position: absolute; left: 26px; top: 196px; list-style: none; }
  .contacts li {
    display: flex; align-items: center; gap: 11px;
    font-size: 17px; color: var(--text-grey);
    height: 24px;
  }
  .contacts svg { width: 14px; height: 14px; fill: var(--text-grey); flex: none; }

  .website {
    position: absolute; right: 32px; top: 243px;
    font-size: 15px; color: var(--text-grey);
  }
</style>
</head>
<body>

  <section class="card card--rounded card--front rounded-front">
    <div class="wordmark"><span class="wordmark__dot"></span>brovix</div>
  </section>

  <section class="card card--rounded card--back rounded-back">
    <div class="wordmark"><span class="wordmark__dot"></span>brovix</div>
    <div class="person">
      <h1 class="person__name">Halyna Dorosh</h1>
      <p class="person__title">Director of Marketing</p>
    </div>
    <div class="divider"></div>
    <p class="address">
      <svg class="address__pin" viewBox="0 0 12 16"><path d="M6 0a6 6 0 0 0-6 6c0 4.5 6 10 6 10s6-5.5 6-10a6 6 0 0 0-6-6zm0 8.5A2.5 2.5 0 1 1 6 3.5a2.5 2.5 0 0 1 0 5z"/></svg>
      20517 - 87 Ave. Edmonton<br>AB, Canada. T6K 4N8
    </p>
    <ul class="contacts">
      <li><svg viewBox="0 0 16 16"><path d="M3.6 1l2.3 3-1.4 1.7c.9 2 2.6 3.8 4.8 4.8L11 9.1l3 2.3-1.2 2.9C7 14.5 1.5 9 1.7 3.2z"/></svg>780.555.0184</li>
      <li><svg viewBox="0 0 16 16"><path d="M1 5c0-2 3-3 7-3s7 1 7 3v1.5h-3.5V5h-7v1.5H1zM3 8h10l1 6H2zm5 1.5a2 2 0 1 0 0 4 2 2 0 0 0 0-4z"/></svg>780.555.0184</li>
      <li><svg viewBox="0 0 16 16"><path d="M1 3h14v1.2L8 9 1 4.2zM1 5.8l7 4.8 7-4.8V13H1z"/></svg>halya.dorosh@quillmail.example</li>
    </ul>
    <p class="website">www.brovix.example</p>
  </section>

  <section class="card card--front square-front">
    <div class="wordmark"><span class="wordmark__dot"></span>brovix</div>
  </section>

  <section class="card card--back square-back">
    <div class="wordmark"><span class="wordmark__dot"></span>brovix</div>
    <div class="person">
      <h1 class="person__name">Halyna Dorosh</h1>
      <p class="person__title">Director of Marketing</p>
    </div>
    <div class="divider"></div>
    <p class="address">
      <svg class="address__pin" viewBox="0 0 12 16"><path d="M6 0a6 6 0 0 0-6 6c0 4.5 6 10 6 10s6-5.5 6-10a6 6 0 0 0-6-6zm0 8.5A2.5 2.5 0 1 1 6 3.5a2.5 2.5 0 0 1 0 5z"/></svg>
      20517 - 87 Ave. Edmonton<br>AB, Canada. T6K 4N8
    </p>
    <ul class="contacts">
      <li><svg viewBox="0 0 16 16"><path d="M3.6 1l2.3 3-1.4 1.7c.9 2 2.6 3.8 4.8 4.8L11 9.1l3 2.3-1.2 2.9C7 14.5 1.5 9 1.7 3.2z"/></svg>780.555.0184</li>
      <li><svg viewBox="0 0 16 16"><path d="M1 5c0-2 3-3 7-3s7 1 7 3v1.5h-3.5V5h-7v1.5H1zM3 8h10l1 6H2zm5 1.5a2 2 0 1 0 0 4 2 2 0 0 0 0-4z"/></svg>780.555.0184</li>
      <li><svg viewBox="0 0 16 16"><path d="M1 3h14v1.2L8 9 1 4.2zM1 5.8l7 4.8 7-4.8V13H1z"/></svg>halya.dorosh@quillmail.example</li>
    </ul>
    <p class="website">www.brovix.example</p>
  </section>

</body>
</html>
```